Business Card - Tidal Lanes

Need Business Card design for company named Tidal Lanes. Software development focused mainly on Brindle Orvix & Zelt Apps. I've attached our logo with both a black and white background. Please add trademark symbol to logo when using.

```html
<!DOCTYPE html>
<html lang="en">
<head>
<meta charset="utf-8">
<title>Tidal Lanes — Business Card</title>
<link rel="stylesheet" href="https://fonts.googleapis.com/css2?family=Open+Sans:wght@400;600;700&display=swap">
<style>
  :root {
    --stage: #e4e4e8;
    --ink: #111111;
    --white: #ffffff;
    --yellow: #f9c315;
    --orange: #f6a033;
    --red: #d8262a;
    --text-dark: #1a1a1a;
  }
  * { box-sizing: border-box; margin: 0; padding: 0; }
  html, body {
    width: 1200px; height: 987px; overflow: hidden;
    background: var(--stage);
    font-family: "Open Sans", Arial, sans-serif;
  }
  .canvas { position: relative; width: 1200px; height: 987px; }
  .card {
    position: absolute; width: 680px; height: 389px;
    border-radius: 34px; overflow: hidden;
    box-shadow: 0 10px 28px rgba(0,0,0,0.18);
  }
  /* Back side */
  .card-back {
    left: 450px; top: 70px;
    background: linear-gradient(135deg, var(--yellow) 0%, var(--orange) 100%);
    display: flex; flex-direction: column; align-items: center; justify-content: center;
    gap: 22px;
  }
  .back-wordmark {
    color: var(--white); font-weight: 700; font-size: 64px; letter-spacing: -1px;
    display: flex; align-items: center; gap: 18px;
  }
  .back-wordmark .mark-square {
    width: 44px; height: 44px; background: var(--white); border-radius: 6px;
  }
  .web-address { color: var(--white); font-size: 18px; letter-spacing: 2px; }
  /* Front side */
  .card-front { left: 80px; top: 530px; background: var(--ink); }
  .card-front svg.wave { position: absolute; inset: 0; }
  .front-wordmark {
    position: absolute; left: 150px; right: 0; top: 78px;
    display: flex; justify-content: center; align-items: center; gap: 14px;
    color: var(--white); font-weight: 700; font-size: 46px; letter-spacing: -1px;
  }
  .front-wordmark .mark-square {
    width: 34px; height: 34px; background: var(--yellow); border-radius: 5px;
  }
  .person { position: absolute; left: 34px; top: 218px; color: var(--text-dark); line-height: 1.25; }
  .person-name { font-size: 24px; font-weight: 700; }
  .person-title { font-size: 17px; }
  .contact {
    position: absolute; right: 30px; bottom: 16px;
    color: var(--text-dark); font-size: 20px; line-height: 1.35; text-align: right;
  }
  .contact .row { display: flex; align-items: center; justify-content: flex-end; gap: 8px; }
  .contact svg { width: 18px; height: 18px; }
</style>
</head>
<body>
<main class="canvas">
  <section class="card card-back">
    <div class="back-wordmark"><span class="mark-square"></span>Tidal Lanes™</div>
    <div class="web-address">www.tidallanes.com</div>
  </section>

  <section class="card card-front">
    <svg class="wave" width="680" height="389" viewBox="0 0 680 389" aria-hidden="true">
      <defs>
        <linearGradient id="band" x1="0" y1="0" x2="1" y2="1">
          <stop offset="0" stop-color="#f9c315"/>
          <stop offset="1" stop-color="#f6a033"/>
        </linearGradient>
      </defs>
      <path d="M0,30 C40,120 120,190 260,215 C420,240 600,250 680,262" fill="none" stroke="#f9c315" stroke-width="4"/>
      <path d="M0,37 C40,127 120,197 260,222 C420,247 600,257 680,269" fill="none" stroke="#d8262a" stroke-width="4"/>
      <path d="M0,44 C40,134 120,204 260,229 C420,254 600,264 680,276 L680,389 L0,389 Z" fill="url(#band)"/>
    </svg>

    <div class="front-wordmark"><span class="mark-square"></span>Tidal Lanes™</div>

    <div class="person">
      <div class="person-name">Your Name</div>
      <div class="person-title">Title</div>
    </div>

    <div class="contact">
      <div class="row">
        <svg viewBox="0 0 24 24" aria-hidden="true"><rect x="7" y="2" width="10" height="20" rx="2" fill="#1a1a1a"/><rect x="9" y="5" width="6" height="9" fill="#f9c315"/></svg>
        <span>555-204-1180</span>
      </div>
      <div class="row">
        <svg viewBox="0 0 24 24" aria-hidden="true"><path d="M3 9c0-3 18-3 18 0v2h-5V9H8v2H3z" fill="#1a1a1a"/><rect x="5" y="12" width="14" height="9" rx="2" fill="#1a1a1a"/></svg>
        <span>555-204-3391</span>
      </div>
      <div class="row"><span>2450 Harbor View Rd, Seabrook, FL 34021</span></div>
    </div>
  </section>
</main>
</body>
</html>
```